KRL Stationery Design Project

Dear Designers,
We need a new stationery design for company to match our new logo.
Designers should provide a design for the following:
1. Business Card: 3.5x2 Inches.
2. Letterhead: A4 size.
3. Envelops: 25x35.5 Cm.
You can keep the Arabic name at the bottom of the logo Or you can use the separate attached Arabic Name.
Please refer to the attached logo guide for design information.
Sample Business Card information:
Name: Tarek Sowan
Position: Operation Manager
Tel: +966 920007164 Ex. 500
Fax: +966 (3)8842617
Mob: +966 (5)00263817
email: tarek@krl-example.com.sa
URL: www.krl-example.com.sa
Address:
Nakheel Heights, Suite 718
Zayed bin Omar Str.
Khobar, 31847
Saudi Arabia
Updates
Dear All,
Please note, we had uploaded our logo along with Arabic writing in Adobe illustrator format (.ai).
Regards,
Karim
Dear All,
A sample data for the business card had been added as per your request.
Regards,
Karim

```html
<!DOCTYPE html>
<html lang="en">
<head>
<meta charset="utf-8">
<title>KRL Business Card</title>
<link href="https://fonts.googleapis.com/css2?family=Source+Sans+3:ital,wght@0,400;0,700;1,700&display=swap" rel="stylesheet">
<style>
  :root {
    --backdrop: #2b2b2b;
    --card: #ffffff;
    --navy: #0f2e52;
    --ink: #3a3a3a;
    --grey: #9a9a9a;
  }
  * { margin: 0; padding: 0; box-sizing: border-box; }
  html, body { width: 960px; height: 1200px; overflow: hidden; }
  body {
    background: var(--backdrop);
    font-family: "Source Sans 3", sans-serif;
    position: relative;
  }
  .card {
    position: absolute;
    background: var(--card);
    border-radius: 30px;
    width: 840px;
    height: 480px;
  }
  .card-front { left: 60px; top: 58px; }
  .card-back { left: 57px; top: 625px; }

  .brand {
    position: absolute;
    left: 0; right: 0;
    display: flex;
    align-items: center;
    justify-content: center;
    gap: 18px;
    color: var(--navy);
    font-weight: 700;
    line-height: 1;
  }
  .brand-mark { background: var(--navy); }
  .card-front .brand { top: 130px; font-size: 92px; }
  .card-front .brand-mark { width: 56px; height: 56px; }
  .card-back .brand { top: 170px; font-size: 130px; }
  .card-back .brand-mark { width: 80px; height: 80px; }

  .holder {
    position: absolute;
    top: 286px; left: 0; right: 0;
    text-align: center;
    color: var(--navy);
    font-size: 29px;
  }
  .holder .role { font-size: 21px; }

  .contact {
    position: absolute;
    top: 340px;
    color: var(--ink);
    font-size: 20px;
    line-height: 28px;
    list-style: none;
  }
  .contact-lines { left: 93px; }
  .contact-address { left: 431px; top: 396px; }
  .contact .key { font-weight: 700; font-style: italic; }
</style>
</head>
<body>
  <section class="card card-front">
    <div class="brand"><span class="brand-mark"></span>KRL</div>
    <p class="holder">Your Name, <span class="role">Designation</span></p>
    <ul class="contact contact-lines">
      <li><span class="key">t</span> : 123-123-1234</li>
      <li><span class="key">f</span> : 123-123-1234</li>
      <li><span class="key">e</span> : info@krl-example.com.sa</li>
      <li><span class="key">w</span> : www.krl-example.com.sa</li>
    </ul>
    <ul class="contact contact-address">
      <li>1234, Suite# 123, Street Name</li>
      <li>State Name, Country Code</li>
    </ul>
  </section>

  <section class="card card-back">
    <div class="brand"><span class="brand-mark"></span>KRL</div>
  </section>
</body>
</html>
```